Business card design for holistic health care clinic

We need a double-sided business card design for our holistic health care clinic that integrates our logo design and also its color scheme. My business is called Valmira. It is an integrative medicine clinic. You have already done the logo for me. Please ensure an elegant and upscale design that is not cluttered, but still has all the necessary information (please see below for details).

Target Market(s)

Wellness, fitness, rehabilitation for educated, well-traveled open-minded clients who are focused on natural, organic, balanced and preventive healthcare and lifestyle.

Industry/Entity Type

Medical

Contact Information for Business Card

Modern, clean.

Number of Pages Required

1 page

Font styles to use
Serif
Sans Serif

Colors

Designer to choose colors to be used in the design.

Requirements
Must have
• Logo on one side, all other information on the other side.
• Other information should include:
• Tobias Wrenfeld - DOE, CPT, LMT
• 4100 East Marrow Drive
• Austin, TX 78119
• 512 555 0148
• 818 555 0192
• info@ValmiraHealth.example
• t.wrenfeld@ValmiraHealth.example
Nice to have
• Darker background on front - but not totally black - shaded/dark gray.

```html
<!DOCTYPE html>
<html lang="en">
<head>
<meta charset="utf-8">
<title>Valmira business card</title>
<link rel="stylesheet" href="https://fonts.googleapis.com/css2?family=Source+Sans+3:wght@400;600;700&display=swap">
<style>
  :root {
    --page: #d9dadc;
    --card-light: #ffffff;
    --card-dark: #2b2c2e;
    --card-dark-edge: #333437;
    --brand-blue: #1e8fd2;
    --text-grey: #4a4a4a;
    --text-light: #e6e6e6;
    --rule-grey: #6c6d70;
    --stripe-grey: #b9bcc0;
  }
  * { box-sizing: border-box; margin: 0; padding: 0; }
  html, body { width: 1200px; height: 960px; overflow: hidden; }
  body {
    background: var(--page);
    font-family: "Source Sans 3", "Segoe UI", sans-serif;
    display: flex; flex-direction: column; align-items: center; justify-content: center;
    gap: 56px;
  }
  .card {
    width: 700px; height: 400px; position: relative; overflow: hidden;
    box-shadow: 0 10px 30px rgba(0,0,0,.18);
  }
  /* Logo side */
  .card--front { background: var(--card-light); }
  .card--front .wordmark {
    position: absolute; left: 0; right: 0; top: 130px; text-align: center;
    font-weight: 700; font-size: 84px; letter-spacing: 2px; color: var(--brand-blue);
    line-height: 1;
  }
  .card--front .tagline {
    position: absolute; left: 218px; top: 268px;
    display: flex; align-items: center; gap: 8px;
    font-weight: 600; font-size: 19px; color: var(--text-grey);
  }
  .tagline .tagline-rule { width: 150px; height: 2px; background: var(--brand-blue); }

  /* Info side */
  .card--back { background: linear-gradient(160deg, var(--card-dark-edge), var(--card-dark)); }
  .card--back .wordmark {
    position: absolute; right: 40px; top: 96px;
    font-weight: 700; font-size: 62px; letter-spacing: 2px; color: var(--brand-blue); line-height: 1;
  }
  .person { position: absolute; left: 44px; top: 62px; }
  .person-name {
    font-weight: 700; font-size: 22px; color: var(--brand-blue); text-transform: uppercase;
    letter-spacing: .5px; line-height: 28px;
  }
  .person-name .credentials { font-size: 13px; font-weight: 600; letter-spacing: 0; }
  .contact-list { list-style: none; margin-top: 8px; }
  .contact-list li {
    display: flex; align-items: center; gap: 12px;
    font-size: 18px; color: var(--text-light); line-height: 25px;
  }
  .contact-list svg { width: 14px; height: 14px; fill: var(--brand-blue); flex: none; }
  .divider {
    position: absolute; left: 44px; right: 40px; top: 240px; height: 1px; background: var(--rule-grey);
  }
  .address {
    position: absolute; right: 40px; top: 262px; text-align: right; font-style: normal;
    font-size: 20px; line-height: 25px; color: var(--text-light);
  }
  .edge-stripe { position: absolute; left: 0; right: 0; bottom: 20px; height: 6px; background: var(--stripe-grey); }
  .edge-band { position: absolute; left: 0; right: 0; bottom: 0; height: 20px; background: var(--brand-blue); }
</style>
</head>
<body>

  <section class="card card--front" aria-label="Card front">
    <div class="wordmark">VALMIRA</div>
    <p class="tagline">helping the body help itself <span class="tagline-rule"></span></p>
  </section>

  <section class="card card--back" aria-label="Card back">
    <div class="person">
      <h1 class="person-name">Tobias Wrenfeld <span class="credentials">- DOE, CPT, LMT</span></h1>
      <ul class="contact-list">
        <li><svg viewBox="0 0 16 16" aria-hidden="true"><path d="M3 1l3 3-1.5 2a9 9 0 0 0 5.5 5.5L12 10l3 3-2 2C6 15 1 10 1 3z"/></svg>512 555 0148</li>
        <li><svg viewBox="0 0 16 16" aria-hidden="true"><path d="M4 0h8a1 1 0 0 1 1 1v14a1 1 0 0 1-1 1H4a1 1 0 0 1-1-1V1a1 1 0 0 1 1-1zm1 2v10h6V2zm3 11a1 1 0 1 0 0 2 1 1 0 0 0 0-2z"/></svg>818 555 0192</li>
        <li><svg viewBox="0 0 16 16" aria-hidden="true"><path d="M0 3h16v10H0zm1 1v.5l7 5 7-5V4z"/></svg>t.wrenfeld@ValmiraHealth.example</li>
        <li><svg viewBox="0 0 16 16" aria-hidden="true"><path d="M0 3h16v10H0zm1 1v.5l7 5 7-5V4z"/></svg>info@ValmiraHealth.example</li>
        <li><svg viewBox="0 0 16 16" aria-hidden="true"><path d="M8 0a8 8 0 1 0 0 16A8 8 0 0 0 8 0zm0 1.5c1 1.5 1.6 3.6 1.6 6.5S9 13 8 14.5C7 13 6.4 10.9 6.4 8S7 3 8 1.5zM1.6 7.3h3.4v1.4H1.6zm9.4 0h3.4v1.4H11z"/></svg>www.ValmiraHealth.example</li>
      </ul>
    </div>
    <div class="wordmark">VALMIRA</div>
    <div class="divider"></div>
    <address class="address">4100 East Marrow Drive<br>Austin, TX 78119</address>
    <div class="edge-stripe"></div>
    <div class="edge-band"></div>
  </section>

</body>
</html>
```